We need a business card design, letterhead design and envelope design for our corporate image

We are looking for a corporate business card design, letterhead and envelope design to match the business card design. Logo is done.

```html
<!DOCTYPE html>
<html lang="en">
<head>
<meta charset="utf-8">
<title>Norvane Business Card</title>
<link rel="stylesheet" href="https://fonts.googleapis.com/css2?family=Open+Sans:ital,wght@0,400;0,700;1,400;1,700&display=swap">
<style>
  :root {
    --backdrop: #2b2b2b;
    --card: #1d1d1d;
    --accent: #f5c400;
    --ink: #ffffff;
    --muted: #e6e6e6;
  }
  * { margin: 0; padding: 0; box-sizing: border-box; }
  html, body {
    width: 1200px;
    height: 900px;
    overflow: hidden;
    background: var(--backdrop);
    font-family: "Open Sans", Arial, sans-serif;
  }
  .canvas {
    width: 1200px;
    height: 900px;
    display: flex;
    align-items: center;
    justify-content: center;
  }
  .business-card {
    position: relative;
    width: 840px;
    height: 480px;
    background: var(--card);
    box-shadow: 0 18px 40px rgba(0,0,0,0.45);
  }
  .brand {
    position: absolute;
    left: 350px;
    top: 122px;
  }
  .brand-name {
    color: var(--ink);
    font-weight: 700;
    font-size: 62px;
    letter-spacing: -1px;
    line-height: 1;
  }
  .identity {
    position: absolute;
    right: 510px;
    top: 300px;
    text-align: right;
  }
  .person-name {
    color: var(--accent);
    font-weight: 700;
    font-style: italic;
    font-size: 22px;
    letter-spacing: 0.5px;
    text-transform: uppercase;
    white-space: nowrap;
  }
  .person-role {
    color: var(--muted);
    font-style: italic;
    font-size: 18px;
    margin-top: 2px;
  }
  .divider {
    position: absolute;
    left: 352px;
    top: 292px;
    width: 2px;
    height: 104px;
    background: var(--accent);
  }
  .contacts {
    position: absolute;
    left: 378px;
    top: 296px;
    list-style: none;
  }
  .contacts li {
    display: flex;
    align-items: center;
    gap: 10px;
    color: var(--ink);
    font-size: 20px;
    line-height: 32px;
    white-space: nowrap;
  }
  .contacts svg {
    width: 16px;
    height: 16px;
    flex: none;
  }
</style>
</head>
<body>
<main class="canvas">
  <section class="business-card">
    <div class="brand">
      <span class="brand-name">Norvane</span>
    </div>

    <div class="identity">
      <p class="person-name">Daniel Hartwell</p>
      <p class="person-role">President</p>
    </div>

    <div class="divider"></div>

    <ul class="contacts">
      <li>
        <svg viewBox="0 0 16 16" aria-hidden="true">
          <path fill="#f5c400" d="M3.6 1.2l2.4 2.6-1.3 1.7c.9 2 2.4 3.6 4.5 4.6l1.7-1.3 2.6 2.4-1.4 2.4C7.2 13.4 2.5 8.6 1.4 3.8z"/>
        </svg>
        <span>555-318-2047</span>
      </li>
      <li>
        <svg viewBox="0 0 16 16" aria-hidden="true">
          <rect x="1" y="3" width="14" height="10" fill="#f5c400"/>
          <path d="M1.5 3.5L8 9l6.5-5.5" stroke="#1d1d1d" stroke-width="1.5" fill="none"/>
        </svg>
        <span>dhartwell@norvane.com</span>
      </li>
      <li>
        <svg viewBox="0 0 16 16" aria-hidden="true">
          <circle cx="8" cy="8" r="7" fill="#f5c400"/>
          <ellipse cx="8" cy="8" rx="3" ry="7" stroke="#1d1d1d" stroke-width="1.2" fill="none"/>
          <path d="M1 8h14" stroke="#1d1d1d" stroke-width="1.2"/>
        </svg>
        <span>www.norvane.com</span>
      </li>
    </ul>
  </section>
</main>
</body>
</html>
```